Healthcare and Professional IT Services Company need a redesigned business card

We are a IT Services company that targets small medical practices and professional business such as Attorneys, Accounts, Architects etc. We want to communicate a professional yet friendly image using recent logo redesign here on ArtHarbor. Like to see the colors blue and orange in the design. Must use the Tall Pine Computing as displayed in the new logo - then also want to incorporate the fish logo as well.

Target Market(s)

Small medical and professional services

Industry/Entity Type

It Company

Contact Information for Business Card

The usual stuff, place for name address phone website. Also maybe our tagline which is "hooked on technology"

Requirements
Must have
• My new logo and the fish somewhere on the card

```html
<!DOCTYPE html>
<html lang="en">
<head>
<meta charset="utf-8">
<title>Tall Pine Computing – Business Card</title>
<link rel="stylesheet" href="https://fonts.googleapis.com/css2?family=Arimo:wght@400;700&display=swap">
<style>
  :root {
    --page: #ecebe8;
    --card: #ffffff;
    --blue-light: #7fb3e4;
    --blue-mid: #5b94d3;
    --blue-deep: #3f75bd;
    --sky: #5cc3ea;
    --ink: #111111;
    --orange: #f08a2c;
    --white: #ffffff;
  }
  * { margin: 0; padding: 0; box-sizing: border-box; }
  html, body { width: 1200px; height: 892px; overflow: hidden; }
  body {
    background: var(--page);
    font-family: "Arimo", Arial, sans-serif;
    position: relative;
  }
  .card {
    position: absolute;
    left: 320px;
    width: 560px;
    height: 320px;
    background: var(--card);
    border-radius: 4px;
    overflow: hidden;
    box-shadow: 0 6px 18px rgba(0,0,0,0.15);
  }
  .card--front { top: 100px; }
  .card--back { top: 472px; }

  .front-art { position: absolute; inset: 0; }

  .holder-name {
    position: absolute;
    left: 28px; top: 30px;
    font-size: 26px;
    font-weight: 400;
    color: var(--white);
    letter-spacing: 0.3px;
    white-space: nowrap;
  }
  .contact-list {
    position: absolute;
    left: 40px; top: 150px;
    padding-left: 14px;
    border-left: 1.5px solid rgba(255,255,255,0.9);
    list-style: none;
  }
  .contact-item {
    display: flex;
    align-items: center;
    gap: 8px;
    height: 22px;
    font-size: 14px;
    color: var(--white);
    white-space: nowrap;
  }
  .contact-icon { width: 13px; height: 13px; flex: none; }

  .brand {
    position: absolute;
    display: flex;
    align-items: center;
    gap: 10px;
    color: var(--sky);
    font-weight: 700;
    white-space: nowrap;
  }
  .brand-dot { border-radius: 50%; background: var(--orange); flex: none; }
  .brand--front { right: 22px; top: 36px; font-size: 22px; }
  .brand--front .brand-dot { width: 22px; height: 22px; }
  .brand--back { left: 50%; top: 50%; transform: translate(-50%, -50%); font-size: 40px; }
  .brand--back .brand-dot { width: 34px; height: 34px; }
</style>
</head>
<body>

<section class="card card--front" aria-label="Business card front">
  <svg class="front-art" width="560" height="320" viewBox="0 0 560 320" aria-hidden="true">
    <defs>
      <linearGradient id="panelBlue" x1="0" y1="0" x2="1" y2="1">
        <stop offset="0" stop-color="var(--blue-light)"/>
        <stop offset="0.55" stop-color="var(--blue-mid)"/>
        <stop offset="1" stop-color="var(--blue-deep)"/>
      </linearGradient>
    </defs>
    <path class="blue-panel" d="M0,0 H260 C265,110 380,190 560,205 V320 H0 Z" fill="url(#panelBlue)"/>
    <path class="swoosh" d="M270,6 C278,112 388,180 535,195 C384,190 266,120 263,6 Z" fill="var(--ink)"/>
  </svg>

  <h1 class="holder-name">Casey Norland</h1>

  <ul class="contact-list">
    <li class="contact-item">
      <svg class="contact-icon" viewBox="0 0 14 14"><rect width="14" height="14" rx="2" fill="var(--white)"/><path d="M4 3.5h2l.6 2-1 1a5 5 0 0 0 2 2l1-1 2 .6v2c-4 .3-6.9-2.6-6.6-6.6z" fill="var(--blue-mid)"/></svg>
      1-888-555-0142
    </li>
    <li class="contact-item">
      <svg class="contact-icon" viewBox="0 0 14 14"><rect width="14" height="14" rx="2" fill="var(--white)"/><rect x="4.5" y="2.5" width="5" height="9" rx="1" fill="var(--blue-mid)"/></svg>
      1300 555 216
    </li>
    <li class="contact-item">
      <svg class="contact-icon" viewBox="0 0 14 14"><rect width="14" height="14" rx="2" fill="var(--white)"/><rect x="3" y="4" width="8" height="6" fill="none" stroke="var(--blue-mid)" stroke-width="1.2"/><path d="M3 4l4 3.2L11 4" fill="none" stroke="var(--blue-mid)" stroke-width="1.2"/></svg>
      info@tallpinecomputing.com.au
    </li>
    <li class="contact-item">
      <svg class="contact-icon" viewBox="0 0 14 14"><rect width="14" height="14" rx="2" fill="var(--white)"/><circle cx="7" cy="7" r="4" fill="none" stroke="var(--blue-mid)" stroke-width="1.2"/><path d="M3 7h8M7 3c-2 2.5-2 5.5 0 8M7 3c2 2.5 2 5.5 0 8" fill="none" stroke="var(--blue-mid)" stroke-width="0.9"/></svg>
      www.tallpinecomputing.com
    </li>
    <li class="contact-item">
      <svg class="contact-icon" viewBox="0 0 14 14"><rect width="14" height="14" rx="2" fill="var(--white)"/><path d="M7 12s-3.2-3.6-3.2-6A3.2 3.2 0 0 1 10.2 6c0 2.4-3.2 6-3.2 6z" fill="var(--blue-mid)"/><circle cx="7" cy="6" r="1.1" fill="var(--white)"/></svg>
      2710 W. Harbor Lane Mesa, Arizona 85201
    </li>
  </ul>

  <div class="brand brand--front">
    <span class="brand-dot"></span>
    <span class="brand-name">Tall Pine Computing</span>
  </div>
</section>

<section class="card card--back" aria-label="Business card back">
  <div class="brand brand--back">
    <span class="brand-dot"></span>
    <span class="brand-name">Tall Pine Computing</span>
  </div>
</section>

</body>
</html>
```